Business Card for Industrial Distributor

We need a business card design for an industrial distributor. We sell machine parts for the manufacturing and oil industry. We would like the cards to look clean and modern but with a touch of industry.

Our colors are blue/white.

Please feel free to visit our website www.korvelpartsco.com

Target Market(s)

mexican manufacturers in the automobile/aerospace industry

Industry/Entity Type

Industrial

Colors
ffffff
0555a3

```html
<!DOCTYPE html>
<html lang="en">
<head>
<meta charset="utf-8">
<title>Korvel Parts – Business Card</title>
<link href="https://fonts.googleapis.com/css2?family=Open+Sans:wght@400;700&display=swap" rel="stylesheet">
<style>
  :root {
    --brand-navy: #26399a;
    --brand-blue: #0555a3;
    --band-light: #1476c0;
    --band-deep: #1f4fa6;
    --back-blue: #2a479c;
    --white: #ffffff;
    --canvas: #ecedef;
  }
  * { margin: 0; padding: 0; box-sizing: border-box; }
  html, body { width: 1200px; height: 900px; overflow: hidden; }
  body {
    background: var(--canvas);
    font-family: "Open Sans", Arial, sans-serif;
    position: relative;
  }
  .card {
    position: absolute;
    overflow: hidden;
    box-shadow: 0 6px 18px rgba(0,0,0,0.18);
  }
  /* Front */
  .card-front {
    left: 77px; top: 34px; width: 589px; height: 364px;
    background: var(--white);
  }
  .front-header {
    height: 156px;
    display: flex; align-items: center;
    padding-left: 33px;
    gap: 14px;
  }
  .brand-dot {
    width: 94px; height: 94px; border-radius: 50%;
    background: var(--brand-blue);
    flex: none;
  }
  .brand-name {
    font-weight: 700;
    font-size: 62px;
    letter-spacing: -1px;
    color: var(--brand-navy);
    line-height: 1;
  }
  .front-band {
    position: absolute; left: 0; top: 156px; right: 0; bottom: 0;
    background: linear-gradient(180deg, var(--band-light) 0%, var(--band-deep) 100%);
    color: var(--white);
    padding: 18px 0 0 31px;
  }
  .holder-name { font-size: 19px; font-weight: 700; line-height: 1.25; }
  .holder-title { font-size: 15px; line-height: 1.3; }
  .contact-list { list-style: none; margin-top: 42px; width: 217px; margin-left: -31px; }
  .contact-list li {
    display: flex; align-items: center; gap: 10px;
    height: 31px; padding-left: 33px;
    font-size: 15px;
    border-bottom: 1px solid rgba(255,255,255,0.3);
    width: 248px;
  }
  .contact-list li:last-child { border-bottom: none; }
  .contact-list svg { width: 12px; height: 12px; flex: none; fill: var(--white); }
  /* Back */
  .card-back {
    left: 388px; top: 505px; width: 567px; height: 352px;
    background: var(--back-blue);
  }
  .back-band {
    position: absolute; left: 0; right: 0; top: 110px; height: 130px;
    background: var(--white);
    display: flex; align-items: center; justify-content: center;
  }
  .back-band .brand-name { font-size: 64px; }
</style>
</head>
<body>
  <section class="card card-front" aria-label="Business card front">
    <header class="front-header">
      <span class="brand-dot" aria-hidden="true"></span>
      <span class="brand-name">Korvel Parts</span>
    </header>
    <div class="front-band">
      <p class="holder-name">Daniel Reyes</p>
      <p class="holder-title">Managing Director</p>
      <ul class="contact-list">
        <li>
          <svg viewBox="0 0 12 12" aria-hidden="true"><path d="M2.4 0.6l1.8 2.2-1 1.2c.7 1.5 1.9 2.7 3.4 3.4l1.2-1 2.2 1.8-1.2 2.2C4.8 10.2 1.8 7.2 0.2 1.8z"/></svg>
          044-987 654 321
        </li>
        <li>
          <svg viewBox="0 0 12 12" aria-hidden="true"><path d="M0.5 2h11v8h-11z M1 2.5l5 4 5-4" fill="var(--white)" stroke="var(--band-deep)" stroke-width="1"/></svg>
          info@korvelpartsco.com
        </li>
        <li>
          <svg viewBox="0 0 12 12" aria-hidden="true"><path d="M5 7l2-2M4.2 5.6L2.6 7.2a1.6 1.6 0 002.2 2.2l1.6-1.6M7.8 6.4l1.6-1.6a1.6 1.6 0 00-2.2-2.2L5.6 4.2" fill="none" stroke="var(--white)" stroke-width="1.4" stroke-linecap="round"/></svg>
          www.korvelpartsco.com
        </li>
      </ul>
    </div>
  </section>

  <section class="card card-back" aria-label="Business card back">
    <div class="back-band">
      <span class="brand-name">Korvel Parts</span>
    </div>
  </section>
</body>
</html>
```